BLS Business Card 2018

Larkmere Chiropractic. We have two locations that we want to advertise on the same card. Brightvale OrthoCore campus address: 3815 Pellham Dr., Suite 240, Flowood, MS 39417. Madison address: 246 Willowmere Dr., Building D., Madison, MS 39284. website: www.drlarkmere-example.com. o:(601)555-0147 f:(601)555-0183

Target Market(s)

Health care decision makers: primary care doctors and mothers

Contact Information for Business Card

I have no idea; up for any suggestions and I'd do much better picking from examples versus describing what I'm looking for. We are in a very high end location and would like the cards to look really sharp.

Requirements
Must have
• My name, Martin R Belvane, D.C.

```html
<!DOCTYPE html>
<html lang="en">
<head>
<meta charset="utf-8">
<title>Larkmere Chiropractic – Business Card</title>
<link rel="stylesheet" href="https://fonts.googleapis.com/css2?family=Cinzel:wght@400;600&family=Open+Sans:wght@400;600&display=swap">
<style>
  :root {
    --stage: #1b1b1b;
    --card: #151515;
    --card-edge: #262626;
    --ink: #f2f2f2;
    --ink-soft: #cfcfcf;
    --rule: #4a4a4a;
    --figure-a: #2c2c2c;
    --figure-b: #151515;
  }
  * { box-sizing: border-box; margin: 0; padding: 0; }
  html, body { width: 1200px; height: 900px; overflow: hidden; }
  body {
    background: var(--stage);
    display: flex;
    flex-direction: column;
    align-items: center;
    justify-content: center;
    gap: 40px;
    font-family: "Open Sans", Arial, sans-serif;
    color: var(--ink);
  }
  .card {
    position: relative;
    width: 560px;
    height: 320px;
    background: var(--card);
    border: 1px solid var(--card-edge);
    border-radius: 22px;
    overflow: hidden;
    box-shadow: 0 14px 30px rgba(0,0,0,.55);
  }
  .figure-art {
    position: absolute;
    left: 0; top: 0;
    width: 250px; height: 320px;
    background: radial-gradient(ellipse at 35% 40%, var(--figure-a) 0%, var(--figure-b) 70%);
  }
  .brand {
    position: absolute;
    display: flex;
    align-items: center;
    gap: 14px;
    font-family: "Cinzel", Georgia, serif;
    font-weight: 400;
    color: var(--ink);
    line-height: 1;
  }
  .brand-dot {
    width: 34px; height: 34px;
    border-radius: 50%;
    border: 1.5px solid var(--ink);
    flex: none;
  }
  .brand-name { display: flex; flex-direction: column; gap: 4px; }
  .brand-name .big { font-size: 30px; letter-spacing: 1px; }
  .brand-name .small { font-size: 19px; letter-spacing: 1.5px; }
  .rule {
    position: absolute;
    height: 1px;
    background: var(--rule);
  }
  /* back */
  .card-back .brand { left: 270px; top: 52px; }
  .card-back .rule { left: 250px; right: 30px; top: 132px; }
  .location {
    position: absolute;
    left: 220px; right: 20px; top: 160px;
    text-align: center;
    font-size: 13px;
    color: var(--ink-soft);
    line-height: 1.7;
  }
  .location .city { font-weight: 600; color: var(--ink); letter-spacing: 1px; }
  /* front */
  .card-front .brand { left: 270px; top: 42px; }
  .card-front .rule { left: 250px; right: 30px; top: 122px; }
  .doctor {
    position: absolute;
    left: 34px; top: 188px;
    font-family: "Cinzel", Georgia, serif;
    font-weight: 600;
    font-size: 21px;
    letter-spacing: 1px;
  }
  .campus {
    position: absolute;
    right: 34px; top: 142px;
    text-align: right;
    font-size: 13px;
    line-height: 1.45;
    color: var(--ink-soft);
  }
  .campus .campus-name { text-transform: uppercase; letter-spacing: .5px; }
  .contacts {
    position: absolute;
    left: 34px; top: 236px;
    list-style: none;
    font-size: 13.5px;
    line-height: 1.6;
    color: var(--ink-soft);
  }
  .contacts li { display: flex; align-items: center; gap: 8px; }
  .contacts svg { width: 12px; height: 12px; fill: var(--ink); flex: none; }
</style>
</head>
<body>

  <section class="card card-back">
    <div class="figure-art" role="img" aria-label="Faint line drawing of a human figure in motion"></div>
    <div class="brand">
      <span class="brand-dot"></span>
      <span class="brand-name"><span class="big">LARKMERE</span><span class="small">CHIROPRACTIC</span></span>
    </div>
    <div class="rule"></div>
    <div class="location">
      <div class="city">MADISON</div>
      <div>246 Willowmere Dr., Building D., Madison, MS 39284.</div>
    </div>
  </section>

  <section class="card card-front">
    <div class="figure-art" role="img" aria-label="Faint line drawing of a human figure in motion"></div>
    <div class="brand">
      <span class="brand-dot"></span>
      <span class="brand-name"><span class="big">LARKMERE</span><span class="small">CHIROPRACTIC</span></span>
    </div>
    <div class="rule"></div>
    <div class="campus">
      <div class="campus-name">Brightvale OrthoCore<br>Campus</div>
      <div>3815 Pellham Dr., Suite 240<br>Flowood, MS 39417</div>
    </div>
    <h1 class="doctor">MARTIN R BELVANE, D.C.</h1>
    <ul class="contacts">
      <li>
        <svg viewBox="0 0 24 24" aria-hidden="true"><path d="M6.6 10.8a15 15 0 0 0 6.6 6.6l2.2-2.2c.3-.3.7-.4 1-.2 1.1.4 2.3.6 3.6.6.6 0 1 .4 1 1V20c0 .6-.4 1-1 1A17 17 0 0 1 3 4c0-.6.4-1 1-1h3.5c.6 0 1 .4 1 1 0 1.3.2 2.5.6 3.6.1.3 0 .7-.2 1z"/></svg>
        (601)555-0147
      </li>
      <li>
        <svg viewBox="0 0 24 24" aria-hidden="true"><path d="M6 2h12v6H6zM3 9h18a1 1 0 0 1 1 1v7h-4v5H6v-5H2v-7a1 1 0 0 1 1-1zm5 7v4h8v-4z"/></svg>
        (601)555-0183
      </li>
      <li>
        <svg viewBox="0 0 24 24" aria-hidden="true"><circle cx="12" cy="12" r="10"/></svg>
        www.drlarkmere-example.com
      </li>
    </ul>
  </section>

</body>
</html>
```